Dunmore Roofing

Want a professional looking business card

Industry/Entity Type

Business

Contact Information for Business Card

Paul Dunmore ( Owner) paul@dunmoreroofing-example.com, www.dunmoreroofing-example.com, Adress: 4172 Township road 43 Larkfield,ON K9X4T2

```html
<!DOCTYPE html>
<html lang="en">
<head>
<meta charset="utf-8">
<title>Dunmore Roofing — Business Card</title>
<link rel="stylesheet" href="https://fonts.googleapis.com/css2?family=Roboto:wght@400;500;700;900&display=swap">
<style>
  :root {
    --page-bg: #e6e6e6;
    --card-black: #1c1c1c;
    --card-black-edge: #2a2a2a;
    --brand-blue: #1f4788;
    --band-blue: rgba(255, 255, 255, 0.1);
    --divider-grey: #8c8c8c;
    --card-white: #ffffff;
    --text-light: #ffffff;
    --front-mark: #6a6a6a;
  }
  * { box-sizing: border-box; margin: 0; padding: 0; }
  html, body {
    width: 1200px; height: 1000px; overflow: hidden;
    background: var(--page-bg);
    font-family: "Roboto", Arial, sans-serif;
  }
  .card {
    position: absolute; left: 269px; width: 662px; height: 380px;
    box-shadow: 0 3px 8px rgba(0,0,0,0.25);
    overflow: hidden;
  }
  .card-front {
    top: 108px;
    background: linear-gradient(135deg, var(--card-black) 0%, var(--card-black-edge) 100%);
    display: flex; align-items: center; justify-content: center;
  }
  .front-wordmark {
    display: flex; align-items: center; gap: 16px;
    color: var(--front-mark); white-space: nowrap;
    font-weight: 900; font-size: 42px; letter-spacing: 2px; text-transform: uppercase;
  }
  .wordmark-square {
    width: 28px; height: 28px; background: currentColor; flex: none;
  }
  .card-back { top: 521px; background: var(--card-white); }
  .back-shapes { position: absolute; inset: 0; }
  .holder {
    position: absolute; left: 38px; top: 46px; color: var(--text-light);
  }
  .holder-name { font-size: 20px; font-weight: 500; line-height: 24px; }
  .holder-role { font-size: 15px; font-weight: 400; line-height: 20px; }
  .address {
    position: absolute; left: 38px; top: 225px; color: var(--text-light);
    font-size: 15px; line-height: 21px; font-style: normal;
  }
  .contacts {
    position: absolute; left: 38px; top: 283px; color: var(--text-light);
    list-style: none; font-size: 15px; line-height: 21px;
  }
  .contacts li { display: flex; align-items: center; gap: 5px; }
  .contacts svg { width: 11px; height: 11px; fill: var(--text-light); flex: none; }
  .back-wordmark {
    position: absolute; left: 378px; width: 276px; top: 170px;
    display: flex; align-items: center; justify-content: center; gap: 9px;
    color: var(--brand-blue); white-space: nowrap;
    font-weight: 900; font-size: 22px; letter-spacing: 1px; text-transform: uppercase;
  }
  .back-wordmark .wordmark-square { width: 18px; height: 18px; }
</style>
</head>
<body>
  <section class="card card-front" aria-label="Card front">
    <div class="front-wordmark"><span class="wordmark-square"></span>Dunmore Roofing</div>
  </section>

  <section class="card card-back" aria-label="Card back">
    <svg class="back-shapes" width="662" height="380" viewBox="0 0 662 380">
      <polygon points="0,0 388,0 313,380 0,380" fill="var(--brand-blue)"/>
      <line x1="395" y1="0" x2="320" y2="380" stroke="var(--divider-grey)" stroke-width="4"/>
      <polygon points="0,40 380,40 370,92 0,92" fill="var(--band-blue)"/>
      <rect x="0" y="40" width="5" height="52" fill="var(--card-white)"/>
    </svg>

    <div class="holder">
      <p class="holder-name">Paul Dunmore</p>
      <p class="holder-role">Owner</p>
    </div>

    <address class="address">
      4172 Township road 43<br>Larkfield, ON K9X4T2
    </address>

    <ul class="contacts">
      <li><svg viewBox="0 0 24 24"><path d="M6.6 10.8a15 15 0 0 0 6.6 6.6l2.2-2.2c.3-.3.7-.4 1-.2 1.1.4 2.3.6 3.6.6.6 0 1 .4 1 1V20c0 .6-.4 1-1 1A17 17 0 0 1 3 4c0-.6.4-1 1-1h3.5c.6 0 1 .4 1 1 0 1.3.2 2.5.6 3.6.1.3 0 .7-.2 1z"/></svg>(613) 555-0147</li>
      <li><svg viewBox="0 0 24 24"><path d="M2 5h20v14H2z"/><path d="M3 6l9 7 9-7" fill="none" stroke="#1f4788" stroke-width="2"/></svg>paul@dunmoreroofing-example.com</li>
      <li><svg viewBox="0 0 24 24"><path d="M12 2a10 10 0 1 0 0 20 10 10 0 0 0 0-20zm6.9 6h-2.9a15 15 0 0 0-1.4-3.6A8 8 0 0 1 18.9 8zM12 4c.8 1.2 1.5 2.5 1.9 4h-3.8c.4-1.5 1.1-2.8 1.9-4zM4.3 14a8 8 0 0 1 0-4h3.4a16 16 0 0 0 0 4zm.8 2h2.9c.3 1.3.8 2.5 1.4 3.6A8 8 0 0 1 5.1 16zM8 8H5.1a8 8 0 0 1 4.3-3.6C8.8 5.5 8.3 6.7 8 8zm4 12c-.8-1.2-1.5-2.5-1.9-4h3.8c-.4 1.5-1.1 2.8-1.9 4zm2.3-6H9.7a14 14 0 0 1 0-4h4.6a14 14 0 0 1 0 4zm.3 5.6c.6-1.1 1.1-2.3 1.4-3.6h2.9a8 8 0 0 1-4.3 3.6zm1.7-5.6a16 16 0 0 0 0-4h3.4a8 8 0 0 1 0 4z"/></svg>www.dunmoreroofing-example.com</li>
    </ul>

    <div class="back-wordmark"><span class="wordmark-square"></span>Dunmore Roofing</div>
  </section>
</body>
</html>
```